Modern Business Card for Larkwell 2018

Our company assumes the best about people. We are creating an online community of entrepreneurs and business leaders who struggle with marketing their business online.

This business card should POP! We recently got a new logo and are launching a new website next month, so our business cards should make a statement that feels:
-Fresh
-Smart
-Trustworthy
-Fun

Target Market(s)

small business owners, entrepreneurs

Industry/Entity Type

Digital Marketing

Contact Information for Business Card

Dimensions: 3.5" x 2"

Font styles to use
Sans Serif

Colors
f37122
ffffff

Requirements
Must have
• We need a business card with a modern, bold design. We will use one side of the card as a lead-generation offer, so text on one side will need to fit up to 140 characters. The business card should stick to our core colors (orange, black, and white).
Nice to have
• We think a vertical "portrait" design could be interesting.
Should not have
• Should not look like a traditional business card. The round icon should stand out from a distance.

```html
<!DOCTYPE html>
<html lang="en">
<head>
<meta charset="utf-8">
<title>Larkwell Business Card</title>
<link href="https://fonts.googleapis.com/css2?family=Montserrat:wght@500;800&family=Oswald:wght@300;400&display=swap" rel="stylesheet">
<style>
  :root {
    --orange: #f37122;
    --white: #ffffff;
    --ink: #2b2b2b;
    --stage: #3a3a3a;
  }
  html, body { margin: 0; padding: 0; }
  body {
    width: 1200px; height: 896px; overflow: hidden;
    background: var(--stage);
    display: flex; flex-direction: column; align-items: center; justify-content: center; gap: 40px;
    font-family: "Montserrat", sans-serif;
  }
  .card {
    position: relative; width: 700px; height: 400px;
    border-radius: 26px; overflow: hidden;
    background: var(--orange); color: var(--white);
    box-shadow: 0 10px 24px rgba(0,0,0,.45);
  }
  .card p { margin: 0; }
  /* Offer side */
  .offer-map {
    position: absolute; inset: 40px 60px 90px 60px;
    background: radial-gradient(ellipse at center, rgba(255,255,255,.12), rgba(255,255,255,0) 70%);
  }
  .offer-brand {
    position: absolute; left: 0; right: 0; top: 110px;
    display: flex; align-items: center; justify-content: center; gap: 18px;
  }
  .brand-dot { width: 46px; height: 46px; border-radius: 50%; background: var(--white); }
  .brand-name {
    font-weight: 800; font-size: 64px; letter-spacing: 1px; line-height: 1;
    text-transform: uppercase;
  }
  .offer-text {
    position: absolute; left: 0; right: 0; top: 212px;
    font-family: "Oswald", sans-serif; font-weight: 300; font-size: 17px; line-height: 1.45; text-align: center;
  }
  .offer-rule {
    position: absolute; left: 70px; right: 70px; top: 300px; height: 1.5px; background: var(--white);
  }
  .offer-tagline {
    position: absolute; left: 0; right: 0; top: 318px; text-align: center;
    font-family: "Oswald", sans-serif; font-weight: 400; font-size: 20px; letter-spacing: .5px;
  }
  /* Contact side */
  .front-art { position: absolute; inset: 0; }
  .front-brand {
    position: absolute; left: 40px; top: 150px;
    font-weight: 800; font-size: 44px; letter-spacing: 1px; text-transform: uppercase; line-height: 1;
  }
  .person { position: absolute; left: 130px; top: 208px; }
  .person-name { font-weight: 500; font-size: 22px; letter-spacing: 1px; text-transform: uppercase; line-height: 1.2; }
  .person-role { font-weight: 500; font-size: 14px; margin-top: 2px; }
  .address { position: absolute; left: 130px; top: 270px; font-size: 14px; line-height: 1.4; font-weight: 500; }
  .contacts { position: absolute; left: 130px; top: 318px; list-style: none; margin: 0; padding: 0; font-size: 14px; line-height: 1.4; font-weight: 500; }
  .contacts li { display: flex; align-items: center; gap: 8px; }
  .contacts svg { width: 11px; height: 11px; fill: var(--white); }
</style>
</head>
<body>

<section class="card card--offer">
  <div class="offer-map" role="img" aria-label="Faint dotted world map texture"></div>
  <div class="offer-brand">
    <span class="brand-dot"></span>
    <span class="brand-name">Larkwell</span>
  </div>
  <p class="offer-text">Get your free Larkwell<br>Starter Package and our marketing guide today at</p>
  <div class="offer-rule"></div>
  <p class="offer-tagline">REACH MORE PEOPLE. MAKE MORE MONEY. CREATE MORE IMPACT.</p>
</section>

<section class="card card--contact">
  <svg class="front-art" viewBox="0 0 700 400" aria-hidden="true">
    <circle cx="540" cy="158" r="175" fill="var(--ink)"/>
    <circle cx="548" cy="150" r="175" fill="var(--white)"/>
    <circle cx="552" cy="146" r="110" fill="var(--orange)"/>
  </svg>
  <div class="front-brand">Larkwell</div>
  <div class="person">
    <p class="person-name">Miles Hartley</p>
    <p class="person-role">Story Marketing Coach</p>
  </div>
  <div class="address">Unit 8, 41 Harbor Lane<br>Eastfield, Northland</div>
  <ul class="contacts">
    <li><svg viewBox="0 0 12 12"><path d="M2.5 1h2l1 3-1.3 1a6 6 0 0 0 2.8 2.8l1-1.3 3 1v2a1 1 0 0 1-1 1A9 9 0 0 1 1.5 2a1 1 0 0 1 1-1z"/></svg>(555) 214-7730</li>
    <li><svg viewBox="0 0 12 12"><path d="M1 2.5h10v7H1zM1.8 3.3 6 6.5l4.2-3.2v-.1H1.8z" fill-rule="evenodd"/></svg>miles@larkwellnow.com</li>
    <li><svg viewBox="0 0 12 12"><circle cx="6" cy="6" r="5"/></svg>www.larkwellnow.com</li>
  </ul>
</section>

</body>
</html>
```